A design led business card for the construction industry

High-end business card to match logo. White logo on dark grey/off black to the front. Matching dark font on white to back, possibly with logo design again.

We offer construction and project management services to commercial and private clients in the UK. Projetcs range from newbuilds, conversion of listed buildings and refurbishments and extensions of existing homes. Our focus is on quality and attention to detail using the highest skills.

Contact Information for Business Card

Name; Dorian Keble BSc
Position; Project Manager
Mobile; 07962 408 175
Tel; 01632 960457
email; dorian@stonevale.co.uk
web; www.stonevale.co.uk
Address; Harrowmere on Wyle, KX4 7PW

Colors

Designer to choose only greyscale colors for use in the design.

Requirements
Must have
• To include the below description of the business,

CONSTRUCTION - PROJECT MANAGEMENT
Nice to have
• The posibility of the top back of the card being used as a ruler. So will have a measurement to scale in mm or an architect scale of 1:50
Should not have
• Should not be portrait

```html
<!DOCTYPE html>
<html lang="en">
<head>
<meta charset="utf-8">
<title>Stonevale – Business Card</title>
<link href="https://fonts.googleapis.com/css2?family=Arimo:wght@400&family=Bebas+Neue&display=swap" rel="stylesheet">
<style>
  :root {
    --backdrop: #0c0c0c;
    --card: #1b1b1b;
    --ink: #ffffff;
    --ink-soft: #c9c9c9;
    --ink-muted: #9a9a9a;
    --rule: #5a5a5a;
  }
  * { margin: 0; padding: 0; box-sizing: border-box; }
  html, body {
    width: 1200px; height: 900px; overflow: hidden;
    background: radial-gradient(ellipse at 55% 40%, #262626 0%, var(--backdrop) 70%);
    font-family: "Arimo", Arial, sans-serif;
  }
  .card {
    position: absolute;
    left: 280px;
    width: 640px; height: 366px;
    background: var(--card);
    box-shadow: 0 14px 30px rgba(0,0,0,.7);
  }
  .card--front { top: 60px; }
  .card--back { top: 474px; }

  /* Front */
  .brand {
    position: absolute; left: 0; right: 0; top: 130px;
    display: flex; flex-direction: column; align-items: center;
  }
  .brand__row { display: flex; align-items: center; gap: 18px; }
  .brand__square { width: 26px; height: 26px; border: 3px solid var(--ink); }
  .brand__name {
    color: var(--ink); font-size: 34px; letter-spacing: 14px;
    margin-right: -14px;
  }
  .brand__tagline {
    margin-top: 16px; color: var(--ink-muted);
    font-size: 13px; letter-spacing: 1.5px;
  }

  /* Back */
  .person {
    position: absolute; left: 60px; top: 110px; width: 250px; text-align: right;
  }
  .person__name {
    font-family: "Bebas Neue", Impact, sans-serif;
    color: var(--ink); font-size: 40px; line-height: 1; letter-spacing: .5px;
  }
  .person__role { color: var(--ink-muted); font-size: 17px; margin-top: 2px; }
  .divider {
    position: absolute; left: 334px; top: 108px; width: 1px; height: 118px;
    background: var(--rule);
  }
  .contacts {
    position: absolute; left: 358px; top: 112px; list-style: none;
  }
  .contacts li {
    display: flex; align-items: center; gap: 8px;
    color: var(--ink-soft); font-size: 18px; line-height: 27px;
  }
  .contacts svg { width: 16px; height: 16px; flex: none; }
  .address {
    position: absolute; left: 0; right: 0; bottom: 58px; text-align: center;
    color: var(--ink-muted); font-size: 18px;
  }
</style>
</head>
<body>
  <section class="card card--front">
    <div class="brand">
      <div class="brand__row">
        <span class="brand__square"></span>
        <span class="brand__name">STONEVALE</span>
      </div>
      <p class="brand__tagline">CONSTRUCTION - PROJECT MANAGEMENT</p>
    </div>
  </section>

  <section class="card card--back">
    <div class="person">
      <h1 class="person__name">DORIAN KEBLE BSC</h1>
      <p class="person__role">Project Manager</p>
    </div>
    <div class="divider"></div>
    <ul class="contacts">
      <li>
        <svg viewBox="0 0 16 16" aria-hidden="true"><path d="M4 1.5l2.2 3-1.4 1.6c.9 2 2.6 3.7 4.6 4.6l1.6-1.4 3 2.2-1.2 2.4C7 13.6 2.4 9 1.6 2.7z" fill="none" stroke="#c9c9c9" stroke-width="1.5" stroke-linejoin="round"/></svg>
        07962 408 175
      </li>
      <li>
        <svg viewBox="0 0 16 16" aria-hidden="true"><rect x="3.5" y="1.5" width="9" height="13" rx="1.5" fill="none" stroke="#c9c9c9" stroke-width="1.5"/><line x1="7" y1="12" x2="9" y2="12" stroke="#c9c9c9" stroke-width="1.5"/></svg>
        01632 960457
      </li>
      <li>
        <svg viewBox="0 0 16 16" aria-hidden="true"><rect x="1" y="3.5" width="14" height="9" fill="#c9c9c9"/><path d="M1 3.5l7 5 7-5" fill="none" stroke="#1b1b1b" stroke-width="1.3"/></svg>
        dorian@stonevale.co.uk
      </li>
      <li>
        <svg viewBox="0 0 16 16" aria-hidden="true"><g fill="none" stroke="#c9c9c9" stroke-width="1.3"><circle cx="8" cy="8" r="6.5"/><ellipse cx="8" cy="8" rx="2.8" ry="6.5"/><line x1="1.5" y1="8" x2="14.5" y2="8"/><line x1="8" y1="1.5" x2="8" y2="14.5"/></g></svg>
        www.stonevale.co.uk
      </li>
    </ul>
    <p class="address">Harrowmere on Wyle, KX4 7PW</p>
  </section>
</body>
</html>
```